I have a logo and need to design the business card and stationery.
Updates

The uploaded logo image named as GREYMARSH CONSTRUCTION which is to be replaced to GREYMARSH CONTRACTS. Kindly add below details and submit the designs- Company name- Greymarsh Engineering Contracts LLP Name & Post- Kelvan Joshi (Designated Partner) Address- Block No.317, Wing C, Tulvo Trade Court, Manek Pural Road, Ruparel Industrial Estate, Goregaon(E), Mumbai - 400 063 Contact- +91 97415 60382 Email- kelvanjoshi@mailbrook.example Website- www.greymarshcontracts.example Contact for Letterhead- +91-22-28754193

Hi Tovin Rahul, We are liking your Design #28860835. We have suggested some changes which are mentioned in feedback. Kindly revert with it asap to finalize this design.

Colors

Designer to choose colors to be used in the design.

```html
<!DOCTYPE html>
<html lang="en">
<head>
<meta charset="utf-8">
<title>Greymarsh Contracts – Stationery</title>
<link href="https://fonts.googleapis.com/css2?family=Open+Sans:wght@400;600;700&family=Poppins:wght@600&display=swap" rel="stylesheet">
<style>
  :root {
    --ink: #2b2b2b;
    --text: #555555;
    --paper: #ffffff;
    --backdrop: #dcdcdc;
    --band: #2e2e2e;
  }
  * { box-sizing: border-box; margin: 0; padding: 0; }
  html, body { width: 1200px; height: 930px; overflow: hidden; }
  body { background: var(--backdrop); font-family: "Open Sans", sans-serif; position: relative; }

  .sheet, .card { position: absolute; background: var(--paper); box-shadow: 0 2px 6px rgba(0,0,0,.25); overflow: hidden; }

  .brand { font-family: "Poppins", sans-serif; font-weight: 600; color: var(--ink); text-align: center; line-height: 1.05; letter-spacing: .04em; }
  .brand-square { background: var(--ink); }

  /* Letterhead */
  .letterhead { left: 104px; top: 118px; width: 529px; height: 679px; }
  .letterhead .brand-square { position: absolute; left: 250px; top: 28px; width: 28px; height: 28px; }
  .letterhead .brand { position: absolute; left: 0; right: 0; top: 64px; font-size: 13px; }
  .letter-body { position: absolute; left: 50px; width: 428px; top: 121px; font-size: 8.2px; color: var(--text); line-height: 1.25; }
  .letter-body .date { margin-bottom: 10px; }
  .letter-body .recipient { margin-bottom: 26px; }
  .letter-body .salutation { margin-bottom: 20px; }
  .letter-body p.para { line-height: 15.2px; text-align: justify; margin-bottom: 15px; }
  .letter-body .closing { margin-top: 30px; }
  .signature { display: block; width: 122px; height: 14px; margin: 11px 0 7px; background: linear-gradient(90deg, #d8d8d8, #ececec); }
  .signer-name { font-size: 10.5px; font-weight: 600; color: #444; }
  .signer-role { margin-top: 4px; }

  .letter-footer { position: absolute; left: 0; top: 640px; width: 461px; height: 39px; background: var(--band); color: #fff; font-size: 8.4px; white-space: nowrap; display: flex; align-items: center; justify-content: center; gap: 5px; }
  .letter-footer span { white-space: nowrap; }
  .letter-footer b { font-weight: 700; }
  .letter-corner { position: absolute; left: 468px; top: 628px; width: 52px; height: 47px; background: var(--band); }

  /* Business cards */
  .card-front { left: 767px; top: 401px; width: 306px; height: 175px; }
  .card-front .brand-square { position: absolute; left: 62px; top: 26px; width: 40px; height: 40px; }
  .card-front .brand { position: absolute; left: 110px; top: 34px; font-size: 12px; text-align: left; }
  .card-person { position: absolute; left: 0; right: 0; top: 76px; text-align: center; color: #222; }
  .card-person .name { font-family: "Poppins", sans-serif; font-weight: 600; font-size: 12.5px; line-height: 1.1; }
  .card-person .role { font-size: 7.5px; line-height: 1.2; padding-bottom: 2px; border-bottom: 1px solid #333; display: inline-block; width: 77px; }
  .card-person .company { margin-top: 5px; font-size: 8.2px; font-weight: 700; }
  .card-person .address { font-size: 7.4px; line-height: 1.4; }
  .card-band { position: absolute; left: 0; top: 151px; width: 273px; height: 24px; background: var(--band); color: #fff; font-size: 7.6px; white-space: nowrap; display: flex; align-items: center; justify-content: center; gap: 4px; }
  .card-band b { font-weight: 700; }
  .card-corner { position: absolute; left: 276px; top: 149px; width: 28px; height: 24px; background: var(--band); }

  .card-back { left: 767px; top: 622px; width: 306px; height: 176px; background: var(--band); }
  .card-back .brand-square { position: absolute; left: 131px; top: 51px; width: 44px; height: 44px; background: #fff; }
  .card-back .brand { position: absolute; left: 0; right: 0; top: 104px; font-size: 13px; color: #fff; }
  .card-back .web { position: absolute; left: 0; right: 0; top: 151px; text-align: center; color: #fff; font-size: 7.4px; }
</style>
</head>
<body>

<section class="sheet letterhead">
  <div class="brand-square"></div>
  <div class="brand">GREYMARSH<br>CONTRACTS</div>

  <div class="letter-body">
    <div class="date">Issuing Date: May 5, 2018</div>
    <div class="recipient">Name Of Employee Mr. XYZABC<br>Address of Employee<br>Address Line 2 etc..</div>
    <div class="salutation">Dear Mr.XYZABC</div>
    <p class="para">Lorem Ipsum has been the industry's standard dummy text ever since the 1500s, when an unknown printer took a galley of type and scrambled it to make a type specimen book. It has survived not only five centuries, but also the leap into electronic typesetting, remaining essentially unchanged. It was popularised in the 1960s with the release of Dryline sheets containing Lorem Ipsum passages, and more recently with desktop publishing software like Quillset Composer including versions of Lorem Ipsum.</p>
    <p class="para">Lorem Ipsum is simply dummy text of the printing and typesetting industry. Lorem Ipsum has been the industry's standard dummy text ever since the 1500s, when an unknown printer took a galley of type and scrambled it to make a type specimen book.</p>
    <p class="para">It has survived not only five centuries, but also the leap into electronic typesetting, remaining essentially unchanged. It was popularised in the 1960s with the release of Dryline sheets containing Lorem IpsumIpsum passages.</p>
    <div class="closing">Yours Sincerely</div>
    <span class="signature" role="img" aria-label="Handwritten signature of Arlen Whitcombe"></span>
    <div class="signer-name">Arlen Whitcombe</div>
    <div class="signer-role">Managing Director</div>
  </div>

  <div class="letter-footer">
    <span><b>P:</b> +91-22-28754193</span><span>|</span>
    <span><b>E:</b> kelvanjoshi@mailbrook.example</span><span>|</span>
    <span><b>W</b> www.greymarshcontracts.example</span>
  </div>
  <div class="letter-corner"></div>
</section>

<section class="card card-front">
  <div class="brand-square"></div>
  <div class="brand">GREYMARSH<br>CONTRACTS</div>
  <div class="card-person">
    <div class="name">Kelvan Joshi</div>
    <div class="role">Designated Partner</div>
    <div class="company">Greymarsh Engineering Contracts LLP</div>
    <div class="address">Block No.317, Wing C, Tulvo Trade Court, Manek Pural Road,<br>Ruparel Industrial Estate, Goregaon(E), Mumbai - 400 063</div>
  </div>
  <div class="card-band">
    <span><b>P:</b> +91 97415 60382</span><span>|</span>
    <span><b>E:</b> kelvanjoshi@mailbrook.example</span>
  </div>
  <div class="card-corner"></div>
</section>

<section class="card card-back">
  <div class="brand-square"></div>
  <div class="brand">GREYMARSH<br>CONTRACTS</div>
  <div class="web">www.greymarshcontracts.example</div>
</section>

</body>
</html>
```